SaaS Early tech startup business card design

Unique design for experience ecommerce platform company. the business cards will be used by executive members. conformance with color code is required.

```html
<!DOCTYPE html>
<html lang="en">
<head>
<meta charset="utf-8">
<title>Qovel Business Card</title>
<link rel="stylesheet" href="https://fonts.googleapis.com/css2?family=Raleway:wght@700;800&family=Roboto:wght@400&display=swap">
<style>
  :root {
    --backdrop: #555555;
    --paper: #ffffff;
    --ink: #2e2e2e;
    --teal: #0e8f9a;
    --deep-blue: #066792;
    --mint: #03b59a;
    --mark: #0a7a95;
    --shadow: rgba(0, 0, 0, 0.55);
  }
  * { margin: 0; padding: 0; box-sizing: border-box; }
  html, body {
    width: 1065px; height: 1200px; overflow: hidden;
    background: var(--backdrop);
  }
  .canvas { position: relative; width: 1065px; height: 1200px; }

  .card {
    position: absolute; width: 583px; height: 362px;
    box-shadow: 3px 3px 4px var(--shadow);
  }
  .card--front {
    left: 292px; top: 218px;
    background: var(--paper);
    border-radius: 0 181px 181px 0;
  }
  .card--back {
    left: 263px; top: 623px;
    background: linear-gradient(180deg, var(--deep-blue) 0%, var(--mint) 100%);
    border-radius: 181px 0 0 181px;
  }

  .holder { position: absolute; left: 28px; top: 82px; }
  .holder__name {
    font-family: "Raleway", sans-serif; font-weight: 700;
    font-size: 21px; color: var(--teal); letter-spacing: 0.2px; line-height: 24px;
  }
  .holder__role {
    font-family: "Roboto", Arial, sans-serif; font-size: 17px;
    color: var(--ink); line-height: 20px;
  }

  .contacts { position: absolute; left: 28px; top: 148px; list-style: none; }
  .contacts__item {
    display: flex; align-items: center; gap: 5px;
    font-family: "Roboto", Arial, sans-serif; font-size: 17px;
    color: var(--ink); height: 22.3px;
  }
  .contacts__item svg { width: 18px; height: 18px; flex: none; }

  .address {
    position: absolute; left: 30px; top: 236px;
    display: flex; gap: 5px;
    font-family: "Roboto", Arial, sans-serif; font-size: 17px;
    color: var(--ink); line-height: 21px;
  }
  .address svg { width: 14px; height: 19px; flex: none; margin-top: 0; }

  .wordmark {
    position: absolute; font-family: "Raleway", sans-serif; font-weight: 800;
    text-transform: lowercase; line-height: 1;
  }
  .card--front .wordmark { left: 302px; top: 118px; font-size: 88px; color: var(--mark); }
  .card--back .wordmark { left: 124px; top: 105px; font-size: 124px; color: var(--paper); }
</style>
</head>
<body>
<div class="canvas">
  <section class="card card--front">
    <div class="holder">
      <h1 class="holder__name">MARCUS HALE</h1>
      <p class="holder__role">Managing Director</p>
    </div>
    <ul class="contacts">
      <li class="contacts__item">
        <svg viewBox="0 0 24 24" aria-hidden="true"><path fill="var(--teal)" d="M6.6 2.5l3 3.2-1.8 2.4c1.2 2.9 3.3 5 6.2 6.2l2.4-1.8 3.2 3-1.9 3.4C10.6 18.5 5.5 13.4 3.2 4.4z"/><path fill="none" stroke="var(--teal)" stroke-width="1.8" stroke-linecap="round" d="M14 3.5a7 7 0 0 1 6.5 6.5M14 7a3.5 3.5 0 0 1 3 3"/></svg>
        044-555 210 734
      </li>
      <li class="contacts__item">
        <svg viewBox="0 0 24 24" aria-hidden="true"><rect x="1" y="5" width="22" height="14" fill="var(--teal)"/><path d="M1 5l11 8 11-8M1 19l8-7M23 19l-8-7" fill="none" stroke="#fff" stroke-width="1.5"/></svg>
        hello@qovelhq.com
      </li>
      <li class="contacts__item">
        <svg viewBox="0 0 24 24" aria-hidden="true"><g fill="none" stroke="var(--teal)" stroke-width="1.8"><circle cx="12" cy="12" r="10"/><ellipse cx="12" cy="12" rx="4.5" ry="10"/><path d="M2 12h20M4 7h16M4 17h16M12 2v20"/></g></svg>
        www.qovelhq.com
      </li>
    </ul>
    <div class="address">
      <svg viewBox="0 0 14 20" aria-hidden="true"><path fill="var(--mark)" d="M7 0a7 7 0 0 0-7 7c0 5 7 13 7 13s7-8 7-13a7 7 0 0 0-7-7z"/><circle cx="7" cy="6.5" r="2.5" fill="#fff"/></svg>
      <p>421, Address line here<br>Country Name, 45452</p>
    </div>
    <p class="wordmark">qovel</p>
  </section>

  <section class="card card--back">
    <p class="wordmark">qovel</p>
  </section>
</div>
</body>
</html>
```